holloway paving service

Needs to have phone number 0418259730 and email markholloway@brightmail.com.au.
ABN 62318470915
name mark holloway

For all your concreting solutions
Excavation
Exposed & colour concrete
House & shed slabs
Driveways
Landing & steps

Contact Information for Business Card

ph 0418259730
email markholloway@brightmail.com.au.
ABN 62318470915
name mark holloway

```html
<!DOCTYPE html>
<html lang="en">
<head>
<meta charset="utf-8">
<title>Holloway Paving Service – Business Card</title>
<link rel="stylesheet" href="https://fonts.googleapis.com/css2?family=Roboto:wght@400;500;700&family=Roboto+Condensed:wght@700&display=swap">
<style>
  :root {
    --bg: #2b2b2b;
    --orange: #f26c23;
    --paper: #f2f2f2;
    --ink: #4a4a4a;
    --white: #ffffff;
  }
  * { margin: 0; padding: 0; box-sizing: border-box; }
  html, body { width: 1200px; height: 960px; overflow: hidden; }
  body {
    position: relative;
    background: var(--bg);
    font-family: "Roboto", Arial, sans-serif;
  }
  .card {
    position: absolute;
    width: 600px;
    height: 342px;
    box-shadow: 0 3px 8px rgba(0,0,0,0.45);
  }
  /* Front */
  .card-front { left: 322px; top: 110px; background: var(--paper); overflow: hidden; }
  .side-band { position: absolute; left: 0; top: 0; width: 67px; height: 100%; background: var(--orange); }
  .brand {
    position: absolute; left: 30px; top: 52px;
    display: flex; align-items: center; gap: 12px;
  }
  .brand-mark { width: 30px; height: 30px; background: var(--orange); }
  .brand-name {
    font-size: 17px; font-weight: 700; color: var(--orange);
    letter-spacing: 0.2px; line-height: 1;
  }
  .contact {
    position: absolute; right: 31px; top: 200px;
    text-align: right; color: var(--ink);
  }
  .contact-name {
    font-family: "Roboto Condensed", "Arial Narrow", sans-serif;
    font-weight: 700; font-size: 23px; color: var(--orange);
    letter-spacing: 0.3px; margin-bottom: 12px;
  }
  .contact-line {
    font-size: 14.5px; line-height: 19.5px;
    display: flex; justify-content: flex-end; align-items: center; gap: 7px;
  }
  .contact-line.abn { margin-right: 2px; margin-bottom: 3px; }
  .contact-icon { width: 13px; height: 13px; flex: none; }
  /* Back */
  .card-back {
    left: 320px; top: 493px; background: var(--orange);
    color: var(--white); text-align: center;
  }
  .back-brand {
    position: absolute; left: 0; right: 0; top: 136px;
    display: flex; justify-content: center; align-items: center; gap: 14px;
  }
  .back-brand-mark { width: 30px; height: 30px; background: var(--white); }
  .back-brand-name { font-size: 30px; font-weight: 700; letter-spacing: 0.5px; }
  .services {
    position: absolute; left: 0; right: 0; top: 270px;
    font-size: 14.5px; line-height: 18px;
  }
  .services .sep { font-size: 10px; margin: 0 5px; vertical-align: 1px; }
</style>
</head>
<body>
  <section class="card card-front" aria-label="Business card front">
    <div class="side-band"></div>
    <div class="brand">
      <span class="brand-mark"></span>
      <span class="brand-name">HOLLOWAY PAVING SERVICE</span>
    </div>
    <div class="contact">
      <div class="contact-name">MARK HOLLOWAY</div>
      <div class="contact-line abn">ABN 62318470915</div>
      <div class="contact-line">0418259730
        <svg class="contact-icon" viewBox="0 0 24 24" aria-hidden="true"><path fill="#f26c23" d="M6.6 10.8a15.1 15.1 0 0 0 6.6 6.6l2.2-2.2c.3-.3.7-.4 1-.2 1.1.4 2.3.6 3.6.6.6 0 1 .4 1 1V20c0 .6-.4 1-1 1C10.6 21 3 13.4 3 4c0-.6.4-1 1-1h3.5c.6 0 1 .4 1 1 0 1.3.2 2.5.6 3.6.1.3 0 .7-.2 1z"/></svg>
      </div>
      <div class="contact-line">markholloway@brightmail.com.au
        <svg class="contact-icon" viewBox="0 0 24 24" aria-hidden="true"><rect x="2" y="5" width="20" height="14" rx="1" fill="#f26c23"/><path d="M3 6l9 7 9-7" fill="none" stroke="#fff" stroke-width="1.6"/></svg>
      </div>
      <div class="contact-line">www.hollowaypaving.com.au
        <svg class="contact-icon" viewBox="0 0 24 24" aria-hidden="true"><circle cx="12" cy="12" r="10" fill="#f26c23"/><path d="M12 2v20M2 12h20M5 6.5c4 2 10 2 14 0M5 17.5c4-2 10-2 14 0" fill="none" stroke="#fff" stroke-width="1.3"/></svg>
      </div>
    </div>
  </section>

  <section class="card card-back" aria-label="Business card back">
    <div class="back-brand">
      <span class="back-brand-mark"></span>
      <span class="back-brand-name">HOLLOWAY PAVING SERVICE</span>
    </div>
    <div class="services">
      <p>Excavation<span class="sep">◆</span>Exposed &amp; colour concrete</p>
      <p>House &amp; shed slabs<span class="sep">◆</span>Driveways<span class="sep">◆</span>Landing &amp; steps</p>
    </div>
  </section>
</body>
</html>
```